A New and modern Business Card for Tarwick Trade Solutions Ltd

New and modern Logo and Business Card Attached is the current logo/business card designCurrently the business is called "Tarwick & Co." or TTS Ltd for short. This is subject to change.This business specialises in Telecoms and Energy. We work with the major networks (QV, K7, etc) and also offer Energy Products saving clients money off their energy bills.These are business to business services.The current design incorporates a Pheonix, indicating rebirth, starting something new.We would like to maintain the Phoenix element but a newer modern style.We love colours in the logo 3 max.The aim of this is to be ultra slick and modern. I envisage Tarwick & Co. on one side of the card with long descriptions on the other side.Side 1:TTS Ltd/Logo?Side 2:TTS Ltd/Logo/Graphic?Brogan & Co.Name:Address:Phone:Email:The design is mostly flexible but must incorporate a Phoenix.For example "Tarwick & Co." with a block phoenix behind the text...up to you.

Industry/Entity Type

Telecommunications

Contact Information for Business Card

Tarwick & Co.
Address:
Name:
Phone:
Email:

Logo Text

Tarwick & Co.

Colors
33a6d7
0792cd
acd037
9bcb3c
f78f20
fece3e

Requirements
Must have
• Phoenix
• 3/4 colours max
• Blue representing Technology (wireless)
• Green for Eco Energy
• Orange for Phoenix
• White business card background
Should not have
• phoenix must not all be red/ orange fire, we are a technology service company and the phoenix colours must represent this. Fire is not representative of our company.

```html
<!DOCTYPE html>
<html lang="en">
<head>
<meta charset="utf-8">
<title>Tarwick &amp; Co. — Business Card</title>
<link rel="stylesheet" href="https://fonts.googleapis.com/css2?family=Montserrat:wght@400;500;700&display=swap">
<style>
  :root {
    --backdrop: #141414;
    --card: #1f1f1f;
    --card-edge: #2a2a2a;
    --ink: #ffffff;
    --ink-muted: #9a9a9a;
    --accent: #acd037;
  }
  * { box-sizing: border-box; margin: 0; padding: 0; }
  html, body {
    width: 1200px; height: 900px; overflow: hidden;
    background: var(--backdrop);
    font-family: "Montserrat", sans-serif;
  }
  .canvas {
    position: relative; width: 1200px; height: 900px;
    display: flex; flex-direction: column; align-items: center; justify-content: center; gap: 40px;
  }
  .card {
    position: relative; width: 700px; height: 400px;
    background: var(--card);
    border: 1px solid var(--card-edge);
    box-shadow: 0 20px 40px rgba(0,0,0,.5);
  }
  .card-front { display: flex; align-items: center; justify-content: center; }
  .wordmark {
    display: flex; align-items: center; gap: 16px;
    font-weight: 400; letter-spacing: 1px; line-height: 1;
  }
  .wordmark-square { width: 14px; height: 14px; }
  .card-front .wordmark { font-size: 58px; color: var(--ink-muted); }
  .card-front .wordmark-square { background: var(--ink-muted); }

  .card-back { display: flex; align-items: center; padding: 0 40px 0 44px; }
  .card-back .wordmark { font-size: 42px; color: var(--ink); width: 340px; }
  .card-back .wordmark-square { background: var(--ink); width: 12px; height: 12px; }
  .divider { width: 2px; height: 220px; background: var(--accent); margin: 0 28px 0 8px; }
  .contact { color: var(--ink); font-size: 15px; line-height: 1.55; }
  .contact-name { color: var(--accent); font-weight: 700; font-size: 24px; letter-spacing: 1px; line-height: 1.1; }
  .contact-role { font-size: 15px; margin-bottom: 12px; }
  .contact-address { margin-bottom: 8px; }
  .contact-line { display: flex; align-items: center; gap: 12px; }
  .contact-line svg { width: 13px; height: 13px; flex: none; }
</style>
</head>
<body>
<main class="canvas">
  <section class="card card-front" aria-label="Card front">
    <div class="wordmark"><span class="wordmark-square"></span>tarwick&amp;co</div>
  </section>

  <section class="card card-back" aria-label="Card back">
    <div class="wordmark"><span class="wordmark-square"></span>tarwick&amp;co</div>
    <div class="divider"></div>
    <div class="contact">
      <p class="contact-name">DANIEL HARTLEY</p>
      <p class="contact-role">Director</p>
      <p class="contact-address">120 Colton Street<br>Sydney NSW 2000 Australia</p>
      <p class="contact-line">
        <svg viewBox="0 0 16 16" aria-hidden="true"><path fill="#acd037" d="M3.5 1 6 1.5 7 5 5.3 6.3a9 9 0 0 0 4.4 4.4L11 9l3.5 1 .5 2.5-2 2C7 14.5 1.5 9 1.5 3z"/></svg>
        +612 9000 4812
      </p>
      <p class="contact-line">
        <svg viewBox="0 0 16 16" aria-hidden="true"><rect x="4" y="1" width="8" height="4" fill="#acd037"/><rect x="1" y="6" width="14" height="6" rx="1" fill="#acd037"/><rect x="4" y="10" width="8" height="5" fill="#acd037"/></svg>
        +612 9000 4813
      </p>
      <p class="contact-line">
        <svg viewBox="0 0 16 16" aria-hidden="true"><rect x="1.5" y="3.5" width="13" height="9" fill="none" stroke="#acd037" stroke-width="1.5"/><path d="M1.5 3.5 8 9l6.5-5.5" fill="none" stroke="#acd037" stroke-width="1.5"/></svg>
        mail@tarwickco.com.au
      </p>
      <p class="contact-line">
        <svg viewBox="0 0 16 16" aria-hidden="true"><g fill="none" stroke="#acd037" stroke-width="1.3"><circle cx="8" cy="8" r="6.5"/><ellipse cx="8" cy="8" rx="3" ry="6.5"/><path d="M1.5 8h13M2.5 4.7h11M2.5 11.3h11"/></g></svg>
        www.tarwickco.com.au
      </p>
    </div>
  </section>
</main>
</body>
</html>
```